Bright and beautiful business card for a coach

I'm a personal and business coach based in Perth, Australia. I need a business card that whilst subtle and elegant, will stand out and appeal on a table full of cards.

My business name is Fern Mentoring and the business card must represent the warmth and brightness implied in the name, without being gimmicky. It must have a warmth and appeal and be easy to read.

I prefer clean, minimalist designs.

It must align with the feel of my website and socials: https://www.fernmentoring-example.com.au/
https://www.instagram.com/fernmentoringau/
https://www.facebook.com/fernmentoringau
Updates

Hi Designers Thank you so much for taking the time to submit designs. I wonder if I could have explained myself a little better. Most of the designs that have been submitted look rather formal and many have quite corporate looking embellishments on them (to my eye). I would like softer, warmer, more organic. I’m open to people playing about and being more abstract, using softer embellishments (e.g the line drawing flowers and grasses I’ve used in my socials) incorporating other colours from my palette or like the social icons in my email signature (in PDF), perhaps playing with size/oversize, playing with the bleed. Please don’t be constrained by what I’ve already done, it merely needs to compliment. I’m sorry if I’m not using the right words or have led you astray. I’m no designer, but I’ve done my website, socials, email signature etc all myself (my logo was a design contest) and I was really hoping for my business card to be something more creative than I could have made with a template. Reminder: No black cards/sides please. Thank you 😊

Target Market(s)

Individuals, most likely but not all female. Creative thinkers. Likely professionals.

Industry/Entity Type

Business & Personal Coach

Contact Information for Business Card

(Fern Mentoring Logo) Name: Greta Pellham; Title: Business & Personal Coach; Phone number: +61 (0)458 913307; Email: greta@fernmentoring-example.com.au; Website: https://fernmentoring-example.com.au; Social icons for Facebook, Instagram & LinkedIn: @fernmentoringAU. Optional strapline: "A thinking partner to help you cut through the noise"

Font styles to use
Sans Serif

Colors
00AB8E
00BBA5
67D7C9
C6EFE9
E9F9F6
59FF00
82FF00
B8FF75
E3FFCB
F4FFEA
FFC000
F8CF3A
FAE287
FDF2CF
FEFAEE

Requirements
Must have
• Must align with feel of my website and socials. Must have a pop of #FFC000 (possibly whole of one side, or at least a block). Bright or white background. Easy to read.
Nice to have
• Possibly incorporate the sunshine/grass picture I have used in website and socials - will upload.
Should not have
• Must not be black or dark. Not impersonal or corporate looking.

```html
<!DOCTYPE html>
<html lang="en">
<head>
<meta charset="utf-8">
<title>Fern Mentoring – Business Card</title>
<link href="https://fonts.googleapis.com/css2?family=Montserrat:wght@400;500;600;700&display=swap" rel="stylesheet">
<style>
  :root {
    --stage: #c9c9cb;
    --sun: #ffc000;
    --sun-soft: #f8cf3a;
    --sun-edge: #e3a400;
    --paper: #ffffff;
    --gold: #f2b51e;
    --gold-deep: #c8861a;
    --text-grey: #3a3a3c;
    --rule-grey: #cfcfcf;
    --meadow-light: #f3f4ee;
    --meadow-mid: #dfe6d2;
    --meadow-deep: #b9c6a4;
  }
  * { box-sizing: border-box; margin: 0; padding: 0; }
  html, body {
    width: 1200px; height: 800px; overflow: hidden;
    background: var(--stage);
    font-family: "Montserrat", sans-serif;
  }
  .canvas { position: relative; width: 1200px; height: 800px; }

  .card {
    position: absolute;
    width: 540px; height: 300px;
    border-radius: 22px;
    overflow: hidden;
    background: var(--paper);
    box-shadow: 0 12px 30px rgba(0,0,0,0.22);
  }
  .card--front { left: 50px; top: 140px; }
  .card--back  { left: 610px; top: 360px; }

  /* Front */
  .front-shape { position: absolute; inset: 0; }
  .identity { position: absolute; left: 58px; top: 216px; }
  .identity__name {
    color: var(--gold-deep); font-weight: 600; font-size: 21px; line-height: 1.1;
    white-space: nowrap;
  }
  .identity__title {
    color: var(--text-grey); font-weight: 400; font-size: 11.5px; margin-top: 4px;
    white-space: nowrap;
  }
  .divider {
    position: absolute; left: 250px; top: 196px;
    width: 1px; height: 70px; background: var(--rule-grey);
  }
  .contacts {
    position: absolute; left: 262px; top: 190px;
    list-style: none;
  }
  .contacts li {
    display: flex; align-items: center; gap: 7px;
    color: var(--text-grey); font-size: 11.5px; font-weight: 400;
    height: 24px; white-space: nowrap;
  }
  .contacts svg { width: 12px; height: 12px; flex: none; }

  /* Back */
  .meadow {
    position: absolute; inset: 0;
    background:
      radial-gradient(circle at 62% 12%, rgba(255,255,255,0.95) 0%, rgba(255,255,255,0.6) 18%, rgba(255,255,255,0) 45%),
      linear-gradient(180deg, var(--meadow-light) 0%, var(--meadow-mid) 55%, var(--meadow-deep) 100%);
    opacity: 0.9;
  }
  .meadow-veil { position: absolute; inset: 0; background: rgba(255,255,255,0.45); }
  .brand {
    position: absolute; left: 0; right: 0; top: 112px;
    text-align: center;
    color: var(--gold-deep); font-weight: 500; font-size: 34px;
    letter-spacing: 0.14em; text-transform: uppercase;
  }
  .handle {
    position: absolute; left: 0; right: 0; top: 222px;
    display: flex; justify-content: center; align-items: center; gap: 8px;
    color: var(--text-grey); font-size: 14px; font-weight: 500;
  }
  .handle__dot {
    width: 16px; height: 16px; border-radius: 50%; background: var(--gold);
  }
</style>
</head>
<body>
<main class="canvas">

  <section class="card card--front" aria-label="Business card front">
    <svg class="front-shape" viewBox="0 0 540 300" width="540" height="300" aria-hidden="true">
      <defs>
        <linearGradient id="sunPanel" x1="0" y1="0" x2="1" y2="1">
          <stop offset="0" stop-color="var(--sun)"/>
          <stop offset="1" stop-color="var(--sun-soft)"/>
        </linearGradient>
      </defs>
      <path d="M0,0 H540 V58 C480,74 430,110 360,130 C290,150 220,150 150,160 C110,166 95,200 60,205 C35,208 18,196 0,200 Z" fill="url(#sunPanel)"/>
      <path d="M540,58 C480,74 430,110 360,130 C290,150 220,150 150,160 C110,166 95,200 60,205 C35,208 18,196 0,200"
            fill="none" stroke="var(--sun-edge)" stroke-width="4"/>
    </svg>

    <div class="identity">
      <p class="identity__name">Greta Pellham</p>
      <p class="identity__title">Business &amp; Personal Coach</p>
    </div>
    <span class="divider"></span>

    <ul class="contacts">
      <li>
        <svg viewBox="0 0 24 24" aria-hidden="true"><path fill="var(--gold)" d="M6.6 10.8a15 15 0 0 0 6.6 6.6l2.2-2.2a1 1 0 0 1 1-.25 11.4 11.4 0 0 0 3.6.57 1 1 0 0 1 1 1V20a1 1 0 0 1-1 1A17 17 0 0 1 3 4a1 1 0 0 1 1-1h3.5a1 1 0 0 1 1 1c0 1.25.2 2.45.57 3.57a1 1 0 0 1-.25 1z"/></svg>
        +61 (0)458 913307
      </li>
      <li>
        <svg viewBox="0 0 24 24" aria-hidden="true"><rect x="2" y="5" width="20" height="14" rx="2" fill="var(--gold)"/><path d="M3 6l9 7 9-7" fill="none" stroke="#fff" stroke-width="1.8"/></svg>
        greta@fernmentoring-example.com.au
      </li>
      <li>
        <svg viewBox="0 0 24 24" aria-hidden="true"><circle cx="12" cy="12" r="10" fill="var(--gold)"/><path d="M2 12h20M12 2c3 3 3 17 0 20M12 2c-3 3-3 17 0 20" fill="none" stroke="#fff" stroke-width="1.5"/></svg>
        fernmentoring-example.com.au
      </li>
    </ul>
  </section>

  <section class="card card--back" aria-label="Business card back">
    <div class="meadow" role="img" aria-label="Soft sunlit grass photograph, faded behind the logo"></div>
    <div class="meadow-veil"></div>
    <p class="brand">Fern Mentoring</p>
    <p class="handle"><span class="handle__dot"></span>@fernmentoringAU</p>
  </section>

</main>
</body>
</html>
```